Wattle Crest Aged Care Centre

We need a website design for an aged care facility in Brisbane (a different one to project already posted) with final design provided as a .psd file.

This website will be built on Dot Net Nuke so design needs to be able to be converted into a DNN skin and containers.

Target Market(s)

• Credibility
• Family orientated
• Establish an online identity
• Download a booking form for tours
• Receive general enquiries
• Feature a phone number
• Advertise career opportunities

Number of Pages Required

1 page

Requirements
Must have
• o The following elements are to be included in the design concepts:
• o Phone number will be featured in banner 07 3842 6170
• o Logo and words Marlowe Care Centre to be featured in banner
• o Area for a flash banner of rotating images on homepage (have attached some images)
• o 3 x buttons to be designed and feature on homepage - Book a Tour, Contact Us and Sign up to our newsletter
• o No colour preference but perhaps keeping with their logo/branding but am open to ideas

```html
<!DOCTYPE html>
<html lang="en">
<head>
<meta charset="utf-8">
<title>Marlowe Care Centre</title>
<link href="https://fonts.googleapis.com/css2?family=Tinos:wght@400;700&family=Noto+Sans:wght@400;700&display=swap" rel="stylesheet">
<style>
  :root {
    --brick: #8f1a0c;
    --rust: #c0581a;
    --ink: #2b2116;
    --green: #2f5a2c;
    --cream: #efeee6;
    --paper: #f2f1ea;
    --beige-top: #e2dabd;
    --beige-bottom: #ede3c3;
    --tan: #e3d8cb;
    --band: #d9c6b3;
    --band-line: #c6a98f;
    --footer-top: #f5eee2;
    --footer-bottom: #fbf3e2;
    --cocoa: #2e1a10;
    --grey-dark: #a9a8a4;
    --grey-light: #e0dfdc;
  }
  * { box-sizing: border-box; margin: 0; padding: 0; }
  html, body { width: 1177px; height: 1200px; overflow: hidden; background: #fff; }
  .page { position: relative; width: 1177px; height: 1200px; font-family: "Noto Sans", Tahoma, sans-serif; color: var(--ink); }
  .block { position: absolute; }

  .hero { left: 0; top: 0; width: 1177px; height: 415px;
    background: linear-gradient(180deg, #c9c6bd 0%, #8b7a60 30%, #6a4a2e 52%, #b49a80 68%, #4f6a3a 82%, #8e8c88 100%); }
  .band { left: 0; width: 1177px; height: 23px;
    background: linear-gradient(180deg, var(--band-line) 0 2px, var(--band) 2px 8px, #efe4d8 8px 16px, var(--band) 16px 21px, var(--band-line) 21px); }
  .band--top { top: 415px; }
  .band--bottom { top: 1079px; }

  .nav { left: 0; top: 438px; width: 1134px; height: 77px; display: flex; list-style: none; }
  .nav__item { position: relative; width: 189px; height: 77px;
    background: linear-gradient(180deg, #fbfbf8 0%, #ecebe4 100%);
    border-right: 1px solid #c9c5bb; border-bottom: 1px solid #cfcbc1;
    font-family: "Tinos", "Times New Roman", serif; font-size: 18px; color: var(--brick);
    display: flex; align-items: center; padding-left: 42px; letter-spacing: 0.2px; }
  .nav__item::after { content: ""; position: absolute; right: 0; bottom: 0; width: 14px; height: 14px;
    background: linear-gradient(135deg, #d8d5cc 0 50%, #9b978e 50%); }
  .nav__item--center { justify-content: center; padding-left: 0; }
  .side-column { left: 1134px; top: 438px; width: 43px; height: 641px; background: var(--tan); border-left: 1px solid #cbbfb1; }

  .identity { left: 0; top: 515px; width: 380px; height: 339px; background: var(--cream);
    display: flex; flex-direction: column; align-items: center; padding-top: 44px; }
  .identity__mark { width: 92px; height: 92px; border-radius: 50%; background: var(--green); }
  .identity__name { margin-top: 18px; font-family: "Tinos", "Times New Roman", serif; font-size: 24px; color: var(--green); }
  .identity__phone { margin-top: 34px; font-family: "Tinos", "Times New Roman", serif; font-size: 33px; color: var(--green); letter-spacing: 0.5px; }

  .mission { left: 380px; top: 515px; width: 754px; height: 339px;
    background: linear-gradient(180deg, var(--beige-top) 0%, var(--beige-bottom) 100%); padding: 26px 40px 0 55px; }
  .heading { font-family: "Tinos", "Times New Roman", serif; font-size: 26px; color: var(--ink); font-weight: 400; }
  .heading__lead { font-size: 33px; color: var(--rust); letter-spacing: -0.5px; }
  .mission__text { margin-top: 14px; font-size: 15.2px; line-height: 21.6px; color: #1f1a12; }

  .newsletter { left: 0; top: 854px; width: 380px; height: 225px;
    background: linear-gradient(90deg, var(--grey-light) 0%, #cfcecb 45%, var(--grey-dark) 100%); }
  .newsletter__icon { position: absolute; left: 24px; top: 36px; width: 138px; height: 178px; border-radius: 14px;
    background: linear-gradient(160deg, #ffffff 0%, #f6a23b 35%, #4a90c8 75%, #f3f3f3 100%); }
  .newsletter__title { position: absolute; left: 184px; top: 30px; font-family: "Tinos", "Times New Roman", serif;
    font-size: 29px; line-height: 34px; color: #9b1b10; letter-spacing: -0.5px; }
  .button { position: absolute; left: 197px; top: 172px; width: 140px; height: 34px;
    background: linear-gradient(180deg, #ffffff 0%, #e4e3df 100%); border: 1px solid #b5b3ae;
    box-shadow: 2px 2px 0 #8d8c88; font-size: 16px; font-weight: 700; color: #6a1a10;
    display: flex; align-items: center; justify-content: center; }

  .tour { left: 380px; top: 854px; width: 754px; height: 225px; background: var(--paper); padding: 26px 0 0 47px; }
  .tour__photo { position: absolute; left: 32px; top: 100px; width: 146px; height: 86px; border: 1px solid #6f5a44;
    background: linear-gradient(135deg, #8a6a45 0%, #c6a57c 40%, #e9e4da 70%, #7a6a5a 100%); }
  .tour__lead { position: absolute; left: 199px; top: 102px; font-size: 16.5px; font-weight: 700; color: #1c140c; }
  .tour__links { position: absolute; left: 199px; top: 138px; list-style: none; }
  .tour__link { display: flex; align-items: center; font-size: 15.5px; line-height: 22px; color: #a01c10; text-decoration: underline; }
  .tour__link svg { margin-right: 8px; flex: none; }

  .footer { left: 0; top: 1100px; width: 1177px; height: 100px;
    background: linear-gradient(180deg, var(--footer-top) 0%, var(--footer-bottom) 100%); }
  .footer__emblem { position: absolute; left: 70px; top: 24px; width: 60px; height: 46px; border-radius: 50%; background: #ddd6cb; }
  .footer__nav { position: absolute; left: 230px; top: 26px; display: flex; list-style: none; font-size: 15.5px; color: #1c140c; }
  .footer__nav li + li::before { content: ":"; color: #c0581a; margin: 0 20px; }
  .footer__legal { position: absolute; left: 420px; top: 52px; font-size: 15.5px; color: #1c140c; }
  .footer__legal span { color: #b0300f; text-decoration: underline; margin-left: 6px; }
  .footer__corner { position: absolute; left: 1134px; top: 0; width: 43px; height: 100px; background: var(--cocoa); }
</style>
</head>
<body>
<div class="page">
  <div class="block hero" role="img" aria-label="Photograph of the centre's front entrance with columns, timber doors and garden beds"></div>
  <div class="block band band--top"></div>

  <ul class="block nav">
    <li class="nav__item">HOME</li>
    <li class="nav__item">ABOUT US</li>
    <li class="nav__item nav__item--center">FACILITIES</li>
    <li class="nav__item nav__item--center">TOURS</li>
    <li class="nav__item nav__item--center">CAREERS</li>
    <li class="nav__item nav__item--center">CONTACT US</li>
  </ul>
  <div class="block side-column"></div>

  <section class="block identity">
    <div class="identity__mark"></div>
    <div class="identity__name">Marlowe Care Centre</div>
    <div class="identity__phone">07 3842 6170</div>
  </section>

  <section class="block mission">
    <h2 class="heading"><span class="heading__lead">OUR</span> mission</h2>
    <p class="mission__text">Tat veros ad molor sequiscipit am ex el digna commodo lorperat landrerate do erillamet prat nonsequat. Ip exero con henim dolorem irit accum nos doloreet, sequat, voloboreet, sum iriusto odiam zzrit luptatis ea faccum quismod tatum iuscil ullum volorem dit nibh etum velesecte feugue faccum venit iustis doloborem nonse feum quat eugiam, con utat praesed magna corpera esequis eugiat nulluptatet, sis nit, cor ilit delismod dui er iure consed magnibh etuer ipsumsa ndiam, volore duiscinim vercipsum autpat pratum nullamet, quam, vel ulla feum volorper sum nulla ad er senis nummy num voluptat ute veleniam iusci estrud endit prat, sectem alis acilit ulpute velesectet dolum vulla facil ex eugait lore elissisi.<br>Osto commy niat, con et ip ex etum eum nibh et nosto dolor si ex eu faci tat erostrud magna faccummy nibh ea feu facipis accummodo ero od dol</p>
  </section>

  <section class="block newsletter">
    <div class="newsletter__icon" role="img" aria-label="Illustration of a newsletter document with a plus badge"></div>
    <h2 class="newsletter__title">SIGN UP<br>TO OUR<br>NEWSLETTER</h2>
    <div class="button">more info</div>
  </section>

  <section class="block tour">
    <h2 class="heading"><span class="heading__lead">BOOK A</span> tour</h2>
    <div class="tour__photo" role="img" aria-label="Photograph of a resident kitchen with timber cabinets"></div>
    <p class="tour__lead">Lorem ipsum dolor sit amet consectetur adipi sitsicingt</p>
    <ul class="tour__links">
      <li class="tour__link"><svg width="10" height="10" viewBox="0 0 10 10"><path d="M1 5h7M5 2l3 3-3 3" stroke="#c0581a" stroke-width="1.4" fill="none"/></svg>Sed do eiusmod tempor incididunt ut labore et dolore magna aliqua.</li>
      <li class="tour__link"><svg width="10" height="10" viewBox="0 0 10 10"><path d="M1 5h7M5 2l3 3-3 3" stroke="#c0581a" stroke-width="1.4" fill="none"/></svg>Ut enim minim veniam, quis noistrud exercitation ullamco laboris.</li>
    </ul>
  </section>

  <div class="block band band--bottom"></div>

  <footer class="block footer">
    <div class="footer__emblem" role="img" aria-label="Faint dove illustration"></div>
    <ul class="footer__nav">
      <li>Home</li><li>About Us</li><li>Facilities</li><li>Tours</li><li>Careers</li><li>Contacts</li>
    </ul>
    <p class="footer__legal">2009 |<span>Privacy policy</span></p>
    <div class="footer__corner"></div>
  </footer>
</div>
</body>
</html>
```